KRT Info Brochure

We need a brochure design for a new not-for-profit organisation that is aimed at providing homeless people with a residence that also provides counselling and vocational training to assist them to find suitable employment at the end of the program.
PLEASE NOTE:
Brochure to be A4.
I know the brochure is quite long, it is really a booklet, but please note that it does not have to have a lot of work done on it, I just want it to look professional and the front cover and inside page to look good.
Also please leave about 2-3 pages at the end as I will be adding in some architect drawings.
Please add in a last page with Contact written at the bottom - we will fill that in later. So please ensure it is editable in PDF.
Thank you so much.
Cheers
Marta

```html
<!DOCTYPE html>
<html lang="en">
<head>
<meta charset="utf-8">
<title>KRT Info Brochure – Inside Spread</title>
<link rel="stylesheet" href="https://fonts.googleapis.com/css2?family=Arimo:wght@400;700&display=swap">
<style>
  :root {
    --backdrop: #e4e4e4;
    --paper: #ffffff;
    --olive: #8f8b3d;
    --olive-dark: #6d6a2a;
    --olive-light: #c9c58a;
    --gold: #f1b32e;
    --ink: #3a3a3a;
    --heading: #8a8633;
  }
  * { box-sizing: border-box; margin: 0; padding: 0; }
  html, body { width: 1200px; height: 847px; overflow: hidden; }
  body {
    background: var(--backdrop);
    font-family: "Arimo", Arial, sans-serif;
    color: var(--ink);
  }
  .spread {
    position: absolute;
    left: 80px; top: 70px;
    width: 1040px; height: 707px;
    display: flex;
    box-shadow: 0 10px 30px rgba(0,0,0,.18);
  }
  .page {
    position: relative;
    width: 520px; height: 707px;
    background: var(--paper);
    overflow: hidden;
  }
  .page-frame { position: absolute; inset: 0; width: 100%; height: 100%; }
  .page-body {
    position: absolute;
    left: 34px; right: 34px; top: 92px; bottom: 96px;
    font-size: 8.6px; line-height: 1.38;
  }
  .section { margin-bottom: 10px; }
  .section h2 {
    font-size: 17px; font-weight: 700;
    color: var(--heading);
    margin-bottom: 4px;
    letter-spacing: -.2px;
  }
  .section p { margin-bottom: 6px; }
  .bullets { list-style: none; margin: 2px 0 6px; }
  .bullets li { position: relative; padding-left: 13px; margin-bottom: 1px; }
  .bullets li::before {
    content: ""; position: absolute; left: 0; top: 2px;
    width: 7px; height: 7px; border-radius: 50%;
    background: var(--gold);
  }
  .photo {
    float: right;
    margin: 0 0 6px 12px;
    border-radius: 2px;
  }
  .photo-study { width: 180px; height: 104px; background: linear-gradient(135deg, #d9cfc3, #a89a8b 55%, #6b6258); }
  .photo-student { width: 190px; height: 108px; background: linear-gradient(135deg, #5f8a7c, #3f6658 55%, #c7b9a6); }
  .photo-carer { width: 170px; height: 96px; background: linear-gradient(135deg, #e8e2dc, #b7a89c 50%, #7d8fb0); }
</style>
</head>
<body>
<main class="spread">

  <section class="page page-left">
    <svg class="page-frame" viewBox="0 0 520 707" aria-hidden="true">
      <path d="M0 0 H520 V40 C380 62 200 78 0 70 Z" fill="var(--olive)"/>
      <rect x="470" y="0" width="50" height="44" fill="var(--olive-light)"/>
      <path d="M0 78 C200 86 380 70 520 48" fill="none" stroke="var(--gold)" stroke-width="3"/>
      <path d="M0 640 C180 612 360 606 520 612 V707 H0 Z" fill="var(--olive)"/>
      <rect x="300" y="608" width="140" height="99" fill="var(--olive-light)" opacity=".55"/>
      <path d="M0 630 C180 602 360 596 520 602" fill="none" stroke="var(--gold)" stroke-width="3"/>
    </svg>
    <div class="page-body">
      <article class="section">
        <div class="photo photo-study" role="img" aria-label="Photo of a young person studying with a mentor"></div>
        <h2>2.3. Learning/Training</h2>
        <p>Life skills are the skills that many people take for granted, like managing money, shopping, cooking and society requirements (eg voting, paying taxes etc). These skills are essential for living independently. Some homeless people do not have all of these skills, either because they lost them through periods of homelessness or because they never acquired them. Helping homeless people acquire life skills can help them move on from homelessness and resettle into the community. Life skills training is different from support, help or assistance in that the aim is to promote self-sufficiency. Life skills can be thought of in terms of four broad categories:</p>
        <ul class="bullets">
          <li>Core or basic skills (eg. numeracy, literacy and information technology)</li>
          <li>Independent living skills (eg. finance, nutrition, employment)</li>
          <li>Social skills (eg. interpersonal skills, conflict resolution, developing self-confidence and social networks)</li>
          <li>Society Requirements (eg. voting, taxation etc)</li>
        </ul>
        <p>It is anticipated that most Residents will need to undertake some aspect of Life Skills, which skills are required will be assessed during the initial Intake phase. Life Skills content will vary widely depending upon the individual requirement.</p>
      </article>
      <article class="section">
        <div class="photo photo-student" role="img" aria-label="Photo of a stressed student resting on a stack of books"></div>
        <h2>2.4. Special Needs</h2>
        <p>According to one study, the number of homeless youth diagnosed with learning disabilities is double the rate of other children. Another study found that 28% of homeless youth have ADD. As such, KRT plans to work one on one with Residents with learning disabilities to assist them to undertake various training options with the final aim of placing them in a suitable employment situation.</p>
      </article>
      <article class="section">
        <h2>2.5. Vocational Education</h2>
        <p>Vocational education is education that prepares people for specific trades, crafts and careers at various levels from a trade, a craft, technician, or a professional position. Residents will work closely with their Case Manager and decide on a way forward for the individual, based on their skills, abilities, likes and dislikes, attitude and aptitude. Appropriate training will be sourced to suit the Residents individual needs and a plan to help the individual Resident to reach his/her goals will be developed.</p>
        <p>KRT will do everything in its power to assist the Resident to achieve their desired outcomes, as vocational skills training is the cornerstone of Residents moving into independent living options.</p>
      </article>
    </div>
  </section>

  <section class="page page-right">
    <svg class="page-frame" viewBox="0 0 520 707" aria-hidden="true">
      <path d="M0 0 H520 V70 C320 76 140 60 0 40 Z" fill="var(--olive)"/>
      <rect x="0" y="0" width="190" height="52" fill="var(--olive-light)" opacity=".6"/>
      <path d="M0 48 C140 70 320 86 520 78" fill="none" stroke="var(--gold)" stroke-width="3"/>
      <path d="M0 612 C160 606 340 612 520 640 V707 H0 Z" fill="var(--olive)"/>
      <path d="M0 602 C160 596 340 602 520 630" fill="none" stroke="var(--gold)" stroke-width="3"/>
    </svg>
    <div class="page-body">
      <article class="section">
        <div class="photo photo-carer" role="img" aria-label="Photo of a carer supporting an elderly woman"></div>
        <h2>2.6. Fitting back into Society</h2>
        <p>Once the Residents are ready to fit back into Society, KRT will assist them every step of the way. The Residents Caseworker will step them through all aspects of independent living assisting them with finding:</p>
        <ul class="bullets">
          <li>Appropriate Employment</li>
          <li>Housing / tenancy agreements</li>
          <li>Connecting utilities</li>
          <li>Furnishing</li>
          <li>Transportation</li>
          <li>Schools</li>
          <li>Churches</li>
          <li>Club/meeting locations</li>
        </ul>
      </article>
      <article class="section">
        <h2>2.7. Outreach / After Care Program</h2>
        <p>Once a Resident has finished the internal program, they will be transitioned over a period of time to become a Client. The Client will be assisted to fit back into society (see above) over a period of time to ensure that they have every chance at success.</p>
        <p>KRT will continue to support Clients once they are in successfully returned to society. The Clients Case Worker will become their 'life coach'. The Case Worker/life coach will check in on the Client on a regular basis. If the Client is struggling the Case Worker/life coach will provide whatever assistance is necessary to keep them on track. The Client will be treated as a part of the KRT family and will be invited to significant events throughout the year.</p>
      </article>
      <article class="section">
        <h2>2.8. Family Groups</h2>
        <p>The age breakdown demonstrates a relatively even spread of homelessness between age groups, with a significant number of Under 12's contributing to the statistic. Children who are experiencing homelessness are almost always in a family group, most commonly with a single mother. Recent research has highlighted the problem of single fathers, who are often reluctant to reveal they have children for fear of losing visitation rights.</p>
        <p>Given the significance of this category, KRT will take up to 5 family groups (4 x 4, 1 x 6) at any one time in specially catered family quarters. In addition, we will also have 2 double rooms and 2 triple rooms for other family groups or couples. The entire family will be put into a program as per their individual requirements, with the aim of transitioning families as soon as possible in order to minimize impact to children and mitigating any future issues. During their time at KRT, parents will undertake the program whilst children will be enrolled at the local regional school, where possible or home schooled by suitably qualified teachers. Families will be given significant support to find appropriate housing, employment and schooling and the parent will be supported and encouraged to find employment or training.</p>
      </article>
    </div>
  </section>

</main>
</body>
</html>
```